Lumen Fitness Personal Training Business

I need a business card design with a logo for my personal training company. I'd like the colors to be a vibrant green and black. I'd like the logo to incorporate an anvil (or something similar). I train hardcore competitive athletes as well as soccer moms trying to get and/or stay in shape. I need a logo that will not pigeon hole me in one category or the other, but at the same time not be too intimidating to soccer moms, but will not be off putting to the more hardcore trainees. The design should be attention grabbing and aesthetic.
Target Market(s)
Hardcore athletes as well as average people just trying to get/stay in shape.
Industry/Entity Type
Training

```html
<!DOCTYPE html>
<html lang="en">
<head>
<meta charset="utf-8">
<title>Lumen Fitness – Business Card</title>
<link rel="stylesheet" href="https://fonts.googleapis.com/css2?family=Open+Sans:wght@400;600;700&display=swap">
<style>
  :root {
    --stage: #1c1c1c;
    --card-front: #ffffff;
    --card-back: #e3e3e3;
    --green: #0aa84f;
    --green-bright: #1ea84b;
    --green-light: #62bd4a;
    --ink: #1a1a1a;
  }
  * { margin: 0; padding: 0; box-sizing: border-box; }
  html, body { width: 1200px; height: 900px; overflow: hidden; }
  body {
    background: var(--stage);
    font-family: "Open Sans", Arial, sans-serif;
    position: relative;
  }
  .card {
    position: absolute;
    width: 434px;
    height: 252px;
    border-radius: 12px;
    overflow: hidden;
  }
  .card--front { left: 155px; top: 307px; background: var(--card-front); }
  .card--back { left: 632px; top: 309px; background: var(--card-back); }

  .card__band {
    position: absolute;
    left: 0;
    right: 0;
    bottom: 0;
    height: 34px;
    background: linear-gradient(180deg, var(--green) 0%, var(--green) 60%, var(--green-light) 100%);
  }

  /* front */
  .brand-mark {
    position: absolute;
    left: 28px;
    top: 62px;
    color: var(--green);
    font-weight: 700;
    font-size: 32px;
    line-height: 1.05;
    letter-spacing: 0.5px;
  }
  .contact {
    position: absolute;
    left: 210px;
    top: 46px;
    color: var(--ink);
  }
  .contact__name { font-size: 19px; font-weight: 700; color: var(--green-bright); line-height: 1.1; }
  .contact__role { font-size: 12.5px; color: var(--green-light); margin-top: 2px; }
  .contact__address { font-size: 12.5px; line-height: 1.15; margin-top: 12px; }
  .contact__list { list-style: none; margin-top: 12px; font-size: 12.5px; line-height: 16.5px; }
  .contact__list li { display: flex; align-items: center; gap: 7px; }
  .contact__list svg { width: 10px; height: 10px; fill: var(--green-bright); flex: none; }

  /* back */
  .back-brand {
    position: absolute;
    left: 80px;
    top: 68px;
    display: flex;
    align-items: center;
    gap: 18px;
  }
  .back-brand__dot { width: 20px; height: 20px; border-radius: 50%; background: var(--green); flex: none; }
  .back-brand__name {
    color: var(--green-bright);
    font-weight: 600;
    font-size: 38px;
    line-height: 1.05;
    letter-spacing: 2px;
  }
</style>
</head>
<body>

<section class="card card--front" aria-label="Business card front">
  <div class="brand-mark">Lumen<br>Fitness</div>

  <div class="contact">
    <p class="contact__name">Daniel Carter</p>
    <p class="contact__role">Managing Director</p>
    <p class="contact__address">1234, Address Goes Here<br>Country Name, 123456</p>
    <ul class="contact__list">
      <li><svg viewBox="0 0 10 10" aria-hidden="true"><path d="M3 0h4a1 1 0 0 1 1 1v8a1 1 0 0 1-1 1H3a1 1 0 0 1-1-1V1a1 1 0 0 1 1-1zm0 1.2v6.6h4V1.2z"/></svg>123-456-7890</li>
      <li><svg viewBox="0 0 10 10" aria-hidden="true"><path d="M0 3.2C1.5 1.6 3.2 1 5 1s3.5.6 5 2.2L8.6 4.6 7 3.8V3H3v.8l-1.6.8zM2.5 5h5L9 9H1z"/></svg>123-456-7890</li>
      <li><svg viewBox="0 0 10 10" aria-hidden="true"><path d="M0 2h10v.8L5 5.8 0 2.8zm0 2 5 3 5-3v4H0z"/></svg>info@youremail.com</li>
      <li><svg viewBox="0 0 10 10" aria-hidden="true"><path d="M6 1.2 8.8 4 7.5 5.3 6.8 4.6l.6-.6L6 2.6 4.6 4l-.7-.7zM4 8.8 1.2 6l1.3-1.3.7.7-.6.6L4 7.4 5.4 6l.7.7zM3.4 6 6 3.4l.6.6L4 6.6z"/></svg>www.yourweb.com</li>
    </ul>
  </div>

  <div class="card__band" role="img" aria-label="Green decorative wave band"></div>
</section>

<section class="card card--back" aria-label="Business card back">
  <div class="back-brand">
    <span class="back-brand__dot" aria-hidden="true"></span>
    <span class="back-brand__name">Lumen<br>Fitness</span>
  </div>
  <div class="card__band" role="img" aria-label="Green decorative wave band"></div>
</section>

</body>
</html>
```